Small environmental consultancy needs a simple but professional web design

We are a boutique environmental consultancyand contracting business located in Margaret River in the South West of Western Australia.

We have two arms
1) Consulting which offers environmental planning, management and assessment services primarily to local government and the development industry.
2) Contracting which implements on site plans and on ground works primarily involving revegetation, bush regeneration and environmental weed control.

We need a simple yet professional web design within the wordpress platform that commmunicates professionalism, experience and technical expertise without appearing too corporate.

Something like this structure appeals:
http://fernquill.net.au/environment-services/
or
http://www.tallowbrookenvironmental.com.au/index.php

(without the image gallery function)

Target Market(s)

Local Government Officers deciding on tenders;
Developers, Engineers, Town Planning consultants looking for environmental expertise

Industry/Entity Type

Business

Number of Pages Required

5+ page

Font styles to use
Sans Serif

Colors
33a6d7
9bcb3c

Requirements
Must have
• Pages required include:
• Home
• Environmental Planning and Management
• Revegetation and Regeneration Implementation (This page can mirror the Environmental Planning and Management page exactly in structure but with different text and images)
• About Us (I think that this page can be relatively simple and generic)
• Contact (I think that this page can be very simple and generic)
Nice to have
• An ability to start out basic and quicikly establish a website presence and then build in additional drop downs and pages over time.
Should not have
• It does not need a photo gallery page;
• It does not need a major amount of space dedicated to social media and blogs etc as this is not currently particularly active area for us

```html
<!DOCTYPE html>
<html lang="en">
<head>
<meta charset="utf-8">
<title>Wandoo Ecoservices</title>
<link rel="stylesheet" href="https://fonts.googleapis.com/css2?family=Open+Sans:wght@400;600;700&family=Oswald:wght@400;500&family=Great+Vibes&display=swap">
<style>
:root{
  --blue:#33a6d7;
  --blue-dark:#1f86b8;
  --blue-pale:#a9d8ee;
  --green:#9bcb3c;
  --green-dark:#6f9e1e;
  --brown:#6b3f1f;
  --text:#555;
  --heading:#222;
  --panel:#f2f2f2;
  --footer:#ebebeb;
  --rule:#d6d6d6;
}
*{margin:0;padding:0;box-sizing:border-box}
html,body{width:1200px;height:2509px;overflow:hidden}
body{font-family:"Open Sans",Arial,sans-serif;color:var(--text);background:#fff;position:relative}
.abs{position:absolute}

/* header */
.site-header{position:absolute;left:0;top:0;width:1200px;height:176px;background:linear-gradient(#f7f7f7,#efefef)}
.brand{position:absolute;left:74px;top:40px;display:flex;align-items:center;gap:16px}
.brand-mark{width:60px;height:60px;border-radius:50%;background:var(--green)}
.brand-name{font-family:"Open Sans",sans-serif;font-weight:600;font-size:40px;color:var(--brown);line-height:1}
.brand-tagline{position:absolute;left:152px;top:92px;font-size:14px;color:var(--brown);letter-spacing:.5px}
.call{position:absolute;right:74px;top:36px;text-align:left}
.call-label{font-size:17px;font-weight:700;color:var(--heading)}
.call-number{font-size:30px;font-weight:600;color:var(--blue);line-height:1.1}
.search{position:absolute;left:912px;top:100px;width:214px;height:30px;background:#fff;border:1px solid #ddd;font-size:12px;color:#888;padding:6px 10px}
.search svg{position:absolute;right:8px;top:7px}

/* nav */
.main-nav{position:absolute;left:0;top:176px;width:1200px;height:42px;background:var(--blue);display:flex;align-items:center;padding-left:76px}
.main-nav a{font-size:13px;font-weight:700;color:#fff;text-decoration:none;padding:0 22px;height:42px;line-height:42px}
.main-nav a.active{background:var(--blue-dark)}

/* slider */
.hero{position:absolute;left:0;top:218px;width:1200px;height:337px;background:linear-gradient(180deg,#8fb3c6 0%,#c98c3f 45%,#6f7a2b 70%,#4c6a22 100%)}
.hero-arrow{position:absolute;top:144px;width:50px;height:50px;border-radius:50%;background:#fff;display:flex;align-items:center;justify-content:center}

/* features */
.feature-img{position:absolute;top:450px;width:290px;height:275px}
.feature{position:absolute;top:740px;width:290px}
.feature h2{font-family:"Oswald",sans-serif;font-weight:500;font-size:25px;color:var(--blue);letter-spacing:.5px}
.feature p{font-size:14px;line-height:20px;margin-top:16px}
.btn-small{display:inline-block;margin-top:26px;background:var(--blue-pale);color:#fff;font-size:10px;font-weight:700;padding:7px 12px;width:102px;position:relative}
.btn-small::after,.btn-green::after{content:"";position:absolute;right:11px;top:50%;margin-top:-4px;border-left:5px solid #fff;border-top:4px solid transparent;border-bottom:4px solid transparent}

/* welcome */
.welcome{position:absolute;left:72px;top:1010px;width:1054px}
.welcome-script{font-family:"Great Vibes",cursive;font-size:36px;color:var(--green-dark);margin-left:22px;line-height:1}
.welcome h1{font-family:"Oswald",sans-serif;font-weight:500;font-size:52px;color:var(--green);line-height:1;margin-top:-4px}
.welcome p{font-size:13px;line-height:20px;margin-top:20px}
.welcome p:first-of-type{margin-top:22px}
.btn-green{display:inline-block;margin-top:38px;background:#a7b98a;color:#fff;font-size:10px;font-weight:700;padding:8px 12px;width:104px;position:relative}

/* testimonials + why */
.section-title{position:absolute;top:1558px;font-family:"Oswald",sans-serif;font-weight:500;font-size:25px;color:var(--heading)}
.testimonial{position:absolute;left:72px;width:514px;background:var(--panel);padding:36px 28px}
.testimonial q{display:block;font-size:13px;line-height:21px;font-style:normal}
.testimonial cite{display:block;font-family:"Oswald",sans-serif;font-style:normal;font-size:15px;color:var(--heading);margin-top:26px}
.why-item{position:absolute;left:612px;width:514px;height:166px}
.why-box{position:absolute;left:55px;top:0;width:459px;height:166px;border:2px solid var(--blue-pale);padding:24px 30px 0 86px}
.why-box h3{font-family:"Oswald",sans-serif;font-weight:500;font-size:17px;color:var(--heading)}
.why-box p{font-size:13px;line-height:20px;margin-top:6px}
.why-icon{position:absolute;left:0;top:25px;width:116px;height:116px;border-radius:50%;background:var(--blue);border:4px solid #fff;display:flex;align-items:center;justify-content:center}

/* footer */
.site-footer{position:absolute;left:0;top:2172px;width:1200px;height:290px;background:var(--footer);border-top:1px solid var(--rule)}
.footer-col{position:absolute;top:42px}
.footer-col h4{font-family:"Oswald",sans-serif;font-weight:500;font-size:17px;color:var(--heading)}
.footer-col p,.footer-col li{font-size:13px;line-height:20px;list-style:none}
.footer-col ul{margin-top:10px}
.call-now{position:absolute;left:72px;top:160px}
.call-now .num{font-family:"Oswald",sans-serif;font-size:28px;color:var(--green);display:flex;align-items:center;gap:8px;margin-top:6px}
.field{position:absolute;background:#fff;border:1px solid #ddd;font-size:13px;color:#aaa;padding:8px 12px}
.field svg{position:absolute;right:10px;top:10px}
.send{position:absolute;left:612px;top:212px;width:158px;height:42px;background:linear-gradient(var(--green),var(--green-dark));color:#fff;font-family:"Oswald",sans-serif;font-size:17px;display:flex;align-items:center;justify-content:center}
.copyright{position:absolute;left:0;top:2462px;width:1200px;height:47px;background:var(--footer);border-top:1px solid var(--rule);font-size:13px;padding:14px 72px}
</style>
</head>
<body>

<header class="site-header">
  <div class="brand"><span class="brand-mark"></span><span class="brand-name">Wandoo Ecoservices</span></div>
  <div class="brand-tagline">Environmental Assessment, Planning &amp; Management</div>
  <div class="call"><div class="call-label">Call Us</div><div class="call-number">0412 638 204</div></div>
  <div class="search">Search
    <svg width="14" height="14" viewBox="0 0 14 14"><circle cx="6" cy="6" r="4.5" fill="none" stroke="#999" stroke-width="1.6"/><line x1="9.3" y1="9.3" x2="13" y2="13" stroke="#999" stroke-width="1.8"/></svg>
  </div>
</header>

<nav class="main-nav">
  <a class="active">HOME</a>
  <a>ENVIRONMENTAL PLANNING AND MANAGEMENT</a>
  <a>REVEGETATION AND BUSH REGENERATION</a>
  <a>ABOUT US</a>
  <a>CONTACT</a>
</nav>

<section class="hero" role="img" aria-label="Sunrise over eucalyptus woodland and green paddock">
  <div class="hero-arrow" style="left:73px"><svg width="14" height="18" viewBox="0 0 14 18"><polyline points="10,2 3,9 10,16" fill="none" stroke="#444" stroke-width="3"/></svg></div>
  <div class="hero-arrow" style="right:73px"><svg width="14" height="18" viewBox="0 0 14 18"><polyline points="4,2 11,9 4,16" fill="none" stroke="#444" stroke-width="3"/></svg></div>
</section>

<svg class="feature-img" style="left:96px" viewBox="0 0 290 275" role="img" aria-label="Orange and purple native pea flowers">
  <defs><linearGradient id="g1" x1="0" y1="0" x2="1" y2="1"><stop offset="0" stop-color="#f4a42a"/><stop offset=".6" stop-color="#e0782a"/><stop offset="1" stop-color="#5a2d6e"/></linearGradient></defs>
  <path d="M160 8 C190 8 280 150 280 200 C280 250 250 262 150 262 C50 262 14 250 14 200 C14 150 120 8 160 8Z" fill="var(--blue)"/>
  <path d="M145 0 C175 0 265 142 265 192 C265 242 235 256 135 256 C35 256 0 242 0 192 C0 142 115 0 145 0Z" fill="url(#g1)" stroke="#fff" stroke-width="5"/>
</svg>
<svg class="feature-img" style="left:457px" viewBox="0 0 290 275" role="img" aria-label="Spiky green leaves with pink native flower">
  <defs><linearGradient id="g2" x1="0" y1="0" x2="1" y2="1"><stop offset="0" stop-color="#9fb07a"/><stop offset=".6" stop-color="#5d7a3f"/><stop offset="1" stop-color="#3f5a2d"/></linearGradient></defs>
  <path d="M160 8 C190 8 280 150 280 200 C280 250 250 262 150 262 C50 262 14 250 14 200 C14 150 120 8 160 8Z" fill="var(--blue)"/>
  <path d="M145 0 C175 0 265 142 265 192 C265 242 235 256 135 256 C35 256 0 242 0 192 C0 142 115 0 145 0Z" fill="url(#g2)" stroke="#fff" stroke-width="5"/>
</svg>
<svg class="feature-img" style="left:818px" viewBox="0 0 290 275" role="img" aria-label="Black cockatoo flying against blue sky">
  <defs><linearGradient id="g3" x1="0" y1="0" x2="0" y2="1"><stop offset="0" stop-color="#4f9ee0"/><stop offset=".7" stop-color="#b8dcf2"/><stop offset="1" stop-color="#dceef8"/></linearGradient></defs>
  <path d="M160 8 C190 8 280 150 280 200 C280 250 250 262 150 262 C50 262 14 250 14 200 C14 150 120 8 160 8Z" fill="var(--blue)"/>
  <path d="M145 0 C175 0 265 142 265 192 C265 242 235 256 135 256 C35 256 0 242 0 192 C0 142 115 0 145 0Z" fill="url(#g3)" stroke="#fff" stroke-width="5"/>
</svg>

<article class="feature" style="left:100px">
  <h2>ABOUT US</h2>
  <p>Lorem ipsum dolor sit amet, consectetur adipisicing elit, sed do eiusmod tempor incididunt ut labore et dolore magna aliqua.</p>
  <span class="btn-small">READ MORE</span>
</article>
<article class="feature" style="left:462px">
  <h2>WHY US?</h2>
  <p>Lorem ipsum dolor sit amet, consectetur adipisicing elit, sed do eiusmod tempor incididunt ut labore et dolore magna aliqua.</p>
  <span class="btn-small">READ MORE</span>
</article>
<article class="feature" style="left:823px">
  <h2>CURRENT PROJECT</h2>
  <p>Lorem ipsum dolor sit amet, consectetur adipisicing elit, sed do eiusmod tempor incididunt ut labore et dolore magna aliqua.</p>
  <span class="btn-small">READ MORE</span>
</article>

<section class="welcome">
  <div class="welcome-script">Welcome to</div>
  <h1>WANDOO ECOSERVICES</h1>
  <p>Lorem ipsum dolor sit amet, consectetuer adipiscing elit, sed diam nonummy nibh euismod tincidunt ut laoreet dolore magna aliquam erat ullamcorper suscipit lobortis nisl ut aliquip ex ea commodo consequat.</p>
  <p>Lorem ipsum dolor sit amet, consectetuer adipiscing elit, sed diam nonummy nibh euismod tincidunt ut laoreet dolore magna aliquam erat volutpat. Ut wisi enim ad minim veniam, quis nostrud exerci tation ullamcorper suscipit lobortis nisl ut aliquip ex ea commodo consequat.Lorem ipsum dolor sit amet, consectetuer adipiscing elit, sed diam nonummy nibh euismod tincidunt ut laoreet dolore magna aliquam erat volutpat. Ut wisi enim ad minim veniam, quis nostrud exerci tation ullamcorper suscipit lobortis nisl ut aliquip ex ea commodo consequat.</p>
  <p>Lorem ipsum dolor sit amet, consectetuer adipiscing elit, sed diam nonummy nibh euismod tincidunt ut laoreet dolore magna aliquam erat volutpat. Ut wisi enim ad minim veniam, quis nostrud exerci tation ullamcorper suscipit lobortis nisl ut aliquip ex ea commodo consequat. Lorem ipsum dolor sit amet, consectetuer adipiscing elit, sed diam nonummy nibh euismod tincidunt ut laoreet dolore magna aliquam erat volutpat. Ut wisi enim ad minim veniam, quis nostrud exerci tation ullamcorper suscipit lobortis nisl ut aliquip ex ea commodo consequat.Lorem ipsum dolor sit amet, consectetuer adipiscing elit, sed diam nonummy nibh euismod tincidunt ut laoreet dolore magna aliquam erat ullamcorper suscipit lobortis nisl ut aliquip ex ea commodo consequat.</p>
  <span class="btn-green">READ MORE</span>
</section>

<h2 class="section-title" style="left:72px">CLIENT'S TESTIMONIALS</h2>
<h2 class="section-title" style="left:612px">WHY US?</h2>

<blockquote class="testimonial" style="top:1625px;height:236px">
  <q>"Lorem ipsum dolor sit amet, consectetuer adipiscing elit, sed diam nonummy nibh euismod tincidunt ut laoreet dolore magna aliquam erat volutpat. Ut wisi enim ad minim veniam, quis nostrud exerci tation ullamcorper suscipit lobortis nisl ut aliquip ex ea commodo consequat.uis nostrud exerci tation ullamcorper suscipit lobortis nisl ut aliquip ex ea commodo consequat."</q>
  <cite>- MARK DALTON</cite>
</blockquote>
<blockquote class="testimonial" style="top:1890px;height:232px">
  <q>"Lorem ipsum dolor sit amet, consectetuer adipiscing elit, sed diam nonummy nibh euismod tincidunt ut laoreet dolore magna aliquam erat volutpat. Ut wisi enim ad minim veniam, quis nostrud exerci tation ullamcorper suscipit lobortis nisl ut aliquip ex ea commodo consequat. uis nostrud exerci tation ullamcorper suscipit lobortis nisl ut aliquip ex ea commodo consequat."</q>
  <cite>-PRIYA</cite>
</blockquote>

<div class="why-item" style="top:1625px">
  <div class="why-box"><h3>LOREM IPSUM DOLOR SIT AMET &nbsp;IPSUM DOLOR SIT AMET</h3><p>Lorem ipsum dolor sit amet, consectetuer adipiscing elit, sed diam &nbsp;suscipit lobortis nisl ut aliquip ex ea commodo consequat.</p></div>
  <div class="why-icon"><svg width="52" height="52" viewBox="0 0 52 52"><path d="M8 44 C8 20 26 8 46 6 C44 28 32 44 8 44Z" fill="#fff"/><path d="M8 44 L32 20" stroke="var(--blue)" stroke-width="3"/></svg></div>
</div>
<div class="why-item" style="top:1795px">
  <div class="why-box"><h3>LOREM IPSUM DOLOR SIT AMET &nbsp;IPSUM DOLOR SIT AMET</h3><p>Lorem ipsum dolor sit amet, consectetuer adipiscing elit, sed diam &nbsp;suscipit lobortis nisl ut aliquip ex ea commodo consequat.</p></div>
  <div class="why-icon"><svg width="56" height="56" viewBox="0 0 56 56"><circle cx="28" cy="22" r="13" fill="#fff"/><path d="M4 30 C10 46 18 50 28 50 C38 50 46 46 52 30 L46 30 C42 40 36 44 28 44 C20 44 14 40 10 30Z" fill="#fff"/></svg></div>
</div>
<div class="why-item" style="top:1965px">
  <div class="why-box"><h3>LOREM IPSUM DOLOR SIT AMET &nbsp;IPSUM DOLOR SIT AMET</h3><p>Lorem ipsum dolor sit amet, consectetuer adipiscing elit, sed diam &nbsp;suscipit lobortis nisl ut aliquip ex ea commodo consequat.</p></div>
  <div class="why-icon"><svg width="56" height="56" viewBox="0 0 56 56" fill="none" stroke="#fff" stroke-width="6"><path d="M18 14 A18 18 0 0 1 44 22"/><path d="M46 36 A18 18 0 0 1 22 46"/><path d="M12 40 A18 18 0 0 1 10 24"/><polygon points="42,14 48,26 36,26" fill="#fff" stroke="none"/></svg></div>
</div>

<footer class="site-footer">
  <div class="footer-col" style="left:72px">
    <h4>ABOUT</h4>
    <ul><li>Environmental Planning and Management</li><li>Revegetation and Bush Regeneration</li><li>Contacts</li></ul>
  </div>
  <div class="footer-col" style="left:375px">
    <h4>WEBSITE</h4>
    <ul><li>www.wandooecoservices.com.au</li></ul>
  </div>
  <div class="footer-col" style="left:612px"><h4>CONTACT US</h4></div>
  <div class="call-now">
    <h4 style="font-family:'Oswald',sans-serif;font-weight:500;font-size:17px;color:var(--heading)">CALL US NOW:</h4>
    <div class="num"><svg width="20" height="22" viewBox="0 0 20 22"><path d="M5 1 L8 7 L6 9 C7 12 9 15 12 16 L14 14 L19 17 L17 21 C9 21 1 12 1 4Z" fill="#666"/></svg>0412 638 204</div>
  </div>
  <div class="field" style="left:612px;top:82px;width:254px;height:36px">Name
    <svg width="16" height="16" viewBox="0 0 16 16"><circle cx="8" cy="5" r="4" fill="#bbb"/><path d="M1 16 C1 10 15 10 15 16Z" fill="#bbb"/></svg></div>
  <div class="field" style="left:873px;top:82px;width:253px;height:36px">E-mail
    <svg width="18" height="14" viewBox="0 0 18 14"><rect width="18" height="14" fill="#bbb"/><polyline points="0,0 9,8 18,0" fill="none" stroke="#fff" stroke-width="1.5"/></svg></div>
  <div class="field" style="left:612px;top:128px;width:514px;height:74px">Message
    <svg width="18" height="16" viewBox="0 0 18 16"><path d="M0 0 H18 V11 H7 L3 15 V11 H0Z" fill="#bbb"/></svg></div>
  <div class="send">SEND MESSAGE</div>
</footer>

<div class="copyright">© 2015 Wandoo Ecoservices. All Rights Reserved.</div>

</body>
</html>
```